Baby Boutique Needs a Business Card Design

We need a modern double sided business card design using the attached logo for Little Wren Nook.

Little Wren Nook is a baby boutique which sells only handmade clothing and accessories for both boys and girls. Our store will live exclusively online.

We would like to only use the colors that have been used in the logo.

Target Market(s)

Potential wholesale clients, Small business owners

Industry/Entity Type

Retail

Contact Information for Business Card

Name Gideon R. Falkner (Owner)
Email sales@littlewrennook.example
Main Phone 555-203-7719
Cell phone 555-203-7746
Website www.LittleWrenNook.example

Font styles to use
Sans Serif

Colors

Designer to choose colors to be used in the design.

Requirements
Must have
• -Would like to have icons that indentify the contact information.
• -Include our website
• -Include our tagline in a small area near the bottom. "Handmade Baby Creations"
• -Would like to include Kinloop and Picstream Icons
• -
Nice to have
• Would like to have a simple back side with the logo.
• Something along the lines of the meadowfield lending card attached.

```html
<!DOCTYPE html>
<html lang="en">
<head>
<meta charset="utf-8">
<title>Little Wren Nook — Business Card</title>
<link rel="stylesheet" href="https://fonts.googleapis.com/css2?family=Poppins:wght@300;400;500&family=Quicksand:wght@400;500&display=swap">
<style>
  :root {
    --stage-dark: #3c3a3b;
    --stage-light: #ffffff;
    --card: #f7f5f8;
    --coral: #dc5a5a;
    --teal: #7ccbbd;
    --ink: #4a4a4a;
    --label: #555555;
  }
  * { margin: 0; padding: 0; box-sizing: border-box; }
  html, body { width: 1200px; height: 963px; overflow: hidden; }
  body { background: var(--stage-dark); font-family: "Poppins", sans-serif; position: relative; }

  .stage-header {
    position: absolute; left: 0; top: 0; width: 1200px; height: 102px;
    background: var(--stage-light);
    display: flex; align-items: center; justify-content: center;
  }
  .stage-header p { font-family: "Poppins", sans-serif; font-weight: 300; font-size: 22px; color: var(--label); margin-top: 4px; }

  .card {
    position: absolute; width: 644px; height: 357px;
    background: var(--card); border-radius: 17px; overflow: hidden;
    box-shadow: 0 1px 3px rgba(0,0,0,0.35);
  }
  .card--front { left: 116px; top: 145px; }
  .card--back { left: 438px; top: 522px; }

  .holder { position: absolute; left: 36px; top: 22px; }
  .holder__name { font-family: "Quicksand", sans-serif; font-weight: 400; font-size: 27px; color: var(--coral); letter-spacing: 0.3px; }
  .holder__role { display: flex; align-items: flex-end; gap: 4px; margin-top: -4px; margin-left: 3px; }
  .holder__role span { font-family: "Poppins", sans-serif; font-weight: 500; font-size: 14px; color: var(--coral); letter-spacing: 1px; line-height: 1; }
  .holder__role i { display: block; width: 171px; height: 1px; background: var(--coral); margin-bottom: 2px; }

  .contact { position: absolute; left: 34px; top: 0; list-style: none; }
  .contact li { position: absolute; left: 0; display: flex; align-items: center; gap: 9px; white-space: nowrap; transform: translateY(-50%); }
  .contact svg { width: 21px; height: 21px; flex: none; }
  .contact span { font-family: "Poppins", sans-serif; font-weight: 300; font-size: 17px; color: var(--ink); }

  .social { position: absolute; left: 34px; top: 274px; display: flex; align-items: center; gap: 12px; }
  .social__item { display: flex; align-items: center; gap: 5px; }
  .social__dot { width: 21px; height: 21px; border: 1.3px solid var(--coral); border-radius: 50%; }
  .social__name { font-family: "Poppins", sans-serif; font-weight: 300; font-size: 12px; color: var(--coral); }

  .brand {
    position: absolute; color: var(--teal);
    font-family: "Poppins", sans-serif; font-weight: 500;
    text-align: center; line-height: 1.05;
  }
  .card--front .brand { left: 367px; top: 142px; width: 200px; font-size: 30px; }
  .card--back .brand { left: 201px; top: 138px; width: 240px; font-size: 36px; }

  .tagline-band {
    position: absolute; left: 0; top: 311px; width: 100%; height: 46px;
    background: var(--coral);
    display: flex; align-items: center; justify-content: center;
  }
  .tagline-band p { font-family: "Quicksand", sans-serif; font-weight: 400; font-size: 20px; color: #fff; letter-spacing: 2.6px; }
</style>
</head>
<body>
  <header class="stage-header"><p>white background</p></header>

  <section class="card card--front" aria-label="Business card front">
    <div class="holder">
      <div class="holder__name">Gideon R. Falkner</div>
      <div class="holder__role"><span>owner</span><i></i></div>
    </div>

    <ul class="contact">
      <li style="top:154px">
        <svg viewBox="0 0 24 24" fill="none" stroke="#dc5a5a" stroke-width="1.3"><circle cx="12" cy="12" r="11"/><path d="M8 7.5l2 -.5 1.2 2.6-1.3 1a6 6 0 0 0 3.5 3.5l1-1.3 2.6 1.2-.5 2c-4.8.4-9-3.8-8.5-8.5z" fill="#dc5a5a" stroke="none"/></svg>
        <span>555-203-7719</span>
      </li>
      <li style="top:186px">
        <svg viewBox="0 0 24 24" fill="none" stroke="#dc5a5a" stroke-width="1.3"><circle cx="12" cy="12" r="11"/><rect x="9" y="6.5" width="6" height="11" rx="1"/><line x1="11" y1="15.5" x2="13" y2="15.5"/></svg>
        <span>555-203-7746</span>
      </li>
      <li style="top:219px">
        <svg viewBox="0 0 24 24" fill="none" stroke="#dc5a5a" stroke-width="1.3"><circle cx="12" cy="12" r="11"/><rect x="7" y="8.5" width="10" height="7" fill="#dc5a5a" stroke="none"/><path d="M7 8.5l5 4 5-4" stroke="#f7f5f8" stroke-width="1"/></svg>
        <span>sales@littlewrennook.example</span>
      </li>
      <li style="top:248px">
        <svg viewBox="0 0 24 24" fill="none" stroke="#dc5a5a" stroke-width="1.3"><circle cx="12" cy="12" r="11"/><circle cx="12" cy="12" r="5.5"/><ellipse cx="12" cy="12" rx="2.3" ry="5.5"/><line x1="6.5" y1="12" x2="17.5" y2="12"/></svg>
        <span>www.LittleWrenNook.example</span>
      </li>
    </ul>

    <div class="social" aria-label="Social media">
      <div class="social__item"><span class="social__dot"></span><span class="social__name">Kinloop</span></div>
      <div class="social__item"><span class="social__dot"></span><span class="social__name">Picstream</span></div>
    </div>

    <div class="brand">Little Wren<br>Nook</div>

    <div class="tagline-band"><p>Handmade Baby Creations</p></div>
  </section>

  <section class="card card--back" aria-label="Business card back">
    <div class="brand">Little Wren<br>Nook</div>
  </section>
</body>
</html>
```